Tidewell-Network Theme For Forums!

We are looking for a theme for our forums. The forums are ran off Invision Power Boards. We have a basic theme on there now but we want more our own feel. If possible have some longboarding accept incorporated in the theme. We want the theme to have some red in it to match our logo. Tidewell-network.com

Target Market(s)

Skatingboarding & Longboarding

Coding

Coded - Design and coding required

Number of Pages Required

1 page

Colors
f04a50

```html
<!DOCTYPE html>
<html lang="en">
<head>
<meta charset="utf-8">
<title>Tidewell-Network Forums</title>
<link href="https://fonts.googleapis.com/css2?family=Open+Sans:wght@400;600;700;800&display=swap" rel="stylesheet">
<style>
:root{
  --red:#f04a50;
  --red-soft:#f7686d;
  --slate:#6b6e72;
  --grey-head:#b1b1b1;
  --grey-row:#eeeeee;
  --grey-strip:#d2d2d2;
  --pale:#f4f5f9;
  --footer:#e3e6ef;
  --ink:#333;
  --frame:#e07aa0;
}
*{box-sizing:border-box;margin:0;padding:0}
html,body{width:1200px;height:975px;overflow:hidden;background:#fff;font-family:"Open Sans",sans-serif;color:var(--ink)}
.page{position:relative;width:1200px;height:975px}
.abs{position:absolute}
.brand{left:22px;top:22px;display:flex;align-items:center;gap:10px;font-weight:800;font-size:34px;color:var(--red);letter-spacing:-.5px}
.brand-mark{width:26px;height:26px;background:var(--red)}
.nav{left:22px;top:90px;width:1156px;height:61px;background:var(--red);display:flex;justify-content:flex-end;align-items:center;padding-right:20px;gap:6px}
.nav a{color:#fff;text-decoration:none;font-size:14.5px;font-weight:600;padding:5px 8px}
.nav a.active{background:#fff;color:var(--red)}
.guest{left:22px;top:160px;width:1156px;height:49px;border:1px solid var(--frame);display:flex;align-items:center;justify-content:center;font-size:14.5px;font-weight:600;color:#444}
.title{left:30px;top:219px;font-size:19px;font-weight:600;color:#444;letter-spacing:.3px;display:flex;gap:18px;align-items:center}
.chev{font-size:18px;font-weight:400}
.login{left:22px;top:254px;width:1156px;height:49px;border:1px solid var(--frame);display:flex;align-items:center;padding:0 13px 0 21px;font-size:14.5px;color:#444}
.login span{flex:1}
.field{width:135px;height:35px;border:1px solid #999;margin-left:10px;display:flex;align-items:center;padding-left:12px;font-size:14.5px;color:#555}
.field.pw{letter-spacing:8px;font-size:12px}
.go{width:54px;height:35px;background:var(--red);color:#fff;font-weight:700;font-size:14.5px;display:flex;align-items:center;justify-content:center;margin-left:10px}
.forum{left:25px;top:312px;width:811px;box-shadow:0 2px 4px rgba(0,0,0,.15)}
.bar{background:var(--slate);color:#fff;font-weight:700;font-size:16.5px;height:27px;display:flex;align-items:center;gap:14px;padding-left:10px}
.bar .chev{font-size:15px}
.grid{display:grid;grid-template-columns:483px 85px 85px 158px}
.grid>div{border-right:1px solid #fff}
.grid>div:last-child{border-right:0}
.cols>div{background:var(--grey-head);height:26px;font-size:13.5px;font-weight:600;color:#444;display:flex;align-items:center;justify-content:center}
.cols>div:first-child{justify-content:flex-start;padding-left:10px}
.row>div{background:var(--grey-row);height:85px;display:flex;align-items:center;justify-content:center;font-size:12px}
.row>div.main{justify-content:flex-start;padding-left:16px;gap:16px}
.badge{width:56px;height:42px;background:var(--red);color:#fff;font-size:16px;display:flex;align-items:center;justify-content:center;flex:none}
.main a{display:block;color:#222;font-size:13px;text-decoration:underline;margin-bottom:6px}
.main p{font-size:12px;color:#333}
.last{font-size:10px;line-height:17px;display:block!important;padding:18px 0 0 28px}
.cookies{left:527px;top:460px;width:309px;height:27px;border:1px solid #555;font-size:12.5px;display:flex;align-items:center;justify-content:center;color:#333}
.stats{left:37px;top:505px;width:799px;height:416px;background:var(--pale)}
.stats .bar{height:29px;padding-left:8px}
.today{background:var(--grey-head);height:27px;display:flex;align-items:center;justify-content:center;font-size:13.5px;font-weight:600;color:#444}
.strip{background:var(--grey-strip);height:31px;display:flex;align-items:center;padding-left:6px;font-size:13.5px;color:#444}
.user{height:85px;display:flex;align-items:center;padding-left:4px;gap:31px}
.user .badge{height:42px}
.user-card{width:351px;height:45px;background:#eef0f6;border-left:2px solid var(--red);box-shadow:0 2px 4px rgba(0,0,0,.18);display:flex;align-items:center;padding-left:34px;font-size:12.5px;color:#444}
.recent{left:849px;top:311px;width:329px;height:610px;background:linear-gradient(160deg,#ef3b42 0%,#f4585e 55%,#fb7478 100%);padding:53px 19px 0 19px}
.recent h2{color:#fff;font-size:17px;font-weight:700;display:flex;justify-content:space-between;align-items:center;padding-left:2px;margin-bottom:42px}
.toggle{width:27px;height:27px;border-radius:50%;background:#fff;color:#333;font-size:14px;display:flex;align-items:center;justify-content:center}
.topic{height:83px;padding:18px 0 0 22px;color:#fff}
.topic.card{background:#fff;color:var(--red);box-shadow:0 2px 6px rgba(0,0,0,.12)}
.topic h3{font-size:17px;font-weight:400;display:flex;align-items:center;gap:10px}
.topic time{font-size:12px;display:block;margin-top:2px}
.footer{left:0;top:921px;width:1200px;height:54px;background:var(--footer);display:flex;align-items:center;justify-content:center;font-size:12.5px;color:#444}
</style>
</head>
<body>
<div class="page">
  <div class="abs brand"><span class="brand-mark"></span>Tidewell-Network</div>

  <nav class="abs nav"><a>Help</a><a class="active">Search</a><a>Member</a><a>Calendar</a></nav>

  <div class="abs guest">Welcome Guest ( Login / Register)</div>

  <h1 class="abs title"><span class="chev">»</span>LONGBOARDS - LOREM IPSUM</h1>

  <div class="abs login">
    <span>Welcome Back,Your last Visit Was, Today 10:00 Am</span>
    <div class="field">User Name</div>
    <div class="field pw">●●●●●</div>
    <div class="go">Go</div>
  </div>

  <section class="abs forum">
    <div class="bar"><span class="chev">»</span>A TEST ROOT</div>
    <div class="grid cols"><div>Forum</div><div>Topics</div><div>Reply</div><div>Last Post Info</div></div>
    <div class="grid row">
      <div class="main"><div class="badge">AST</div><div><a>A Test Forum</a><p>Illo inventore veritatis et quasi architecto beatae sunt explicabo.</p></div></div>
      <div>1</div><div>1</div>
      <div class="last">June 1, 2018,10:20 Am<br><b style="font-weight:600">In:</b> Welcome<br><b style="font-weight:600">By:</b> AST Team</div>
    </div>
  </section>

  <div class="abs cookies">Delete Cookies Set by the board - Mark AllasUnread</div>

  <section class="abs stats">
    <div class="bar"><span class="chev">»</span>BOARD STATISTICS</div>
    <div class="today">Todays Topic - Lorem Ipsum</div>
    <div class="strip">2 Users Active in the past 15 mins</div>
    <div class="user">
      <div class="badge"><svg width="34" height="14" viewBox="0 0 34 14"><rect x="1" y="2" width="32" height="5" rx="2.5" fill="#fff"/><circle cx="9" cy="10" r="2.5" fill="#fff"/><circle cx="25" cy="10" r="2.5" fill="#fff"/></svg></div>
      <div class="user-card">jhsrhaguhak</div>
    </div>
    <div class="strip">2 Users Active in the past 15 mins</div>
    <div class="user">
      <div class="badge"><svg width="26" height="30" viewBox="0 0 26 30"><rect x="2" y="1" width="8" height="28" rx="4" fill="none" stroke="#fff" stroke-width="2"/><rect x="16" y="1" width="8" height="28" rx="4" fill="none" stroke="#fff" stroke-width="2"/></svg></div>
      <div class="user-card">jhsrhaguhak</div>
    </div>
    <div class="strip">2 Users Active in the past 15 mins</div>
    <div class="user">
      <div class="badge"><svg width="34" height="14" viewBox="0 0 34 14"><rect x="1" y="2" width="32" height="5" rx="2.5" fill="#fff"/><circle cx="9" cy="10" r="2.5" fill="#fff"/><circle cx="25" cy="10" r="2.5" fill="#fff"/></svg></div>
      <div class="user-card">jhsrhaguhak</div>
    </div>
  </section>

  <aside class="abs recent">
    <h2>RECENTLY ADDED TOPICS <span class="toggle">-</span></h2>
    <div class="topic card"><h3>Longboard By Rafe <svg width="16" height="14" viewBox="0 0 16 14"><path d="M10 4H3v9h9V9" fill="none" stroke="currentColor" stroke-width="2"/><path d="M7 8l7-6M10 1h5v5" fill="none" stroke="currentColor" stroke-width="2"/></svg></h3><time>June 01,2018 &nbsp;10:20 Am</time></div>
    <div class="topic"><h3>Longboard By Rafe <svg width="16" height="14" viewBox="0 0 16 14"><path d="M10 4H3v9h9V9" fill="none" stroke="currentColor" stroke-width="2"/><path d="M7 8l7-6M10 1h5v5" fill="none" stroke="currentColor" stroke-width="2"/></svg></h3><time>June 01,2018 &nbsp;10:20 Am</time></div>
    <div class="topic card"><h3>Longboard By Rafe <svg width="16" height="14" viewBox="0 0 16 14"><path d="M10 4H3v9h9V9" fill="none" stroke="currentColor" stroke-width="2"/><path d="M7 8l7-6M10 1h5v5" fill="none" stroke="currentColor" stroke-width="2"/></svg></h3><time>June 01,2018 &nbsp;10:20 Am</time></div>
    <div class="topic"><h3>Longboard By Rafe <svg width="16" height="14" viewBox="0 0 16 14"><path d="M10 4H3v9h9V9" fill="none" stroke="currentColor" stroke-width="2"/><path d="M7 8l7-6M10 1h5v5" fill="none" stroke="currentColor" stroke-width="2"/></svg></h3><time>June 01,2018 &nbsp;10:20 Am</time></div>
    <div class="topic card"><h3>Longboard By Rafe <svg width="16" height="14" viewBox="0 0 16 14"><path d="M10 4H3v9h9V9" fill="none" stroke="currentColor" stroke-width="2"/><path d="M7 8l7-6M10 1h5v5" fill="none" stroke="currentColor" stroke-width="2"/></svg></h3><time>June 01,2018 &nbsp;10:20 Am</time></div>
  </aside>

  <footer class="abs footer">Copyrights© 2018 . All Rights Reserved.</footer>
</div>
</body>
</html>
```